Laser Tattoo Removal Business Cards

We are looking for a professional business card design for a laser tattoo removal business. Ideally looking for a black business card design. The name of the business is Brightline Tattoo Removal. We place our cards at local tattoo shops so we ideally are looking for something trendy/edgy to draw both male and female clientele in.

Target Market(s)

Male/Female ages 18-60

Contact Information for Business Card

black background ideally.. hoping to stay within greys, whites and black

Font styles to use
Serif
Sans Serif

Colors
121212
a9a9a9
5c5c5c
f5f5f5
ffffff
7f7f7f
606060
848484
9d9d9d

Requirements
Must have
• Employee Info:
• Melissa Thornbury
• Chief Executive Offer
• m: 919.537.2846
• w: 919.362.4178
• f: 919.685.3907
• mthornbury@brightlinetattooremoval.example
• Address:
• 4615 Oakmere Pkwy, Suite 210
• Raleigh, NC 27654
• Website:
• www.brightlinetattooremoval.example
Nice to have
• Myabe business name on back or logo on back and employee info on the front

```html
<!DOCTYPE html>
<html lang="en">
<head>
<meta charset="utf-8">
<title>Brightline Tattoo Removal — Business Cards</title>
<link href="https://fonts.googleapis.com/css2?family=Lato:wght@400;700;900&display=swap" rel="stylesheet">
<style>
  :root {
    --ink: #121212;
    --card-dark: #1c1c1c;
    --grey-dark: #5c5c5c;
    --grey-mid: #7f7f7f;
    --grey-light: #a9a9a9;
    --paper: #ffffff;
    --paper-soft: #f5f5f5;
    --stage: #2a2a2a;
  }
  * { box-sizing: border-box; margin: 0; padding: 0; }
  html, body { width: 1200px; height: 900px; overflow: hidden; }
  body {
    background: var(--stage);
    font-family: "Lato", sans-serif;
    position: relative;
  }
  .card {
    position: absolute;
    width: 600px;
    height: 343px;
    overflow: hidden;
    box-shadow: 0 18px 40px rgba(0,0,0,.45);
  }

  /* Back of card */
  .card--back {
    left: 90px; top: 80px;
    background: var(--card-dark);
  }
  .card--back .wordmark {
    position: absolute; left: 0; right: 0; top: 92px;
    text-align: center; color: var(--grey-dark);
  }
  .card--back .website {
    position: absolute; left: 0; right: 0; bottom: 40px;
    text-align: center; color: var(--paper);
    font-weight: 700; font-size: 15px; letter-spacing: 2.5px;
  }

  /* Wordmark */
  .wordmark { font-weight: 400; line-height: 1; }
  .wordmark__name { display: block; font-size: 60px; letter-spacing: 3px; }
  .wordmark__service { display: block; font-size: 21px; letter-spacing: 6px; margin-top: 16px; }

  /* Front of card */
  .card--front {
    left: 510px; top: 480px;
    background: var(--paper);
  }
  .card--front .wordmark {
    position: absolute; left: 30px; width: 340px; top: 48px;
    text-align: center; color: var(--ink);
  }
  .card--front .wordmark__name { font-size: 46px; }
  .card--front .wordmark__service { font-size: 17px; margin-top: 12px; color: var(--grey-dark); }

  .person {
    position: absolute; right: 44px; top: 52px;
    text-align: right; color: var(--ink);
    font-size: 13px; line-height: 1.35;
  }
  .person__name { font-size: 16px; }
  .person__name strong { font-weight: 900; }
  .person__title { color: var(--grey-dark); font-size: 12.5px; }
  .person__address { margin-top: 18px; font-weight: 900; font-size: 14px; }
  .person-rule {
    position: absolute; right: 26px; top: 40px;
    width: 3px; height: 112px; background: var(--ink);
  }

  .contact-tab {
    position: absolute; left: 0; bottom: 0;
    width: 42px; height: 130px;
    background: var(--ink);
    border-top-right-radius: 16px;
    display: flex; flex-direction: column; justify-content: space-evenly; align-items: center;
    padding: 8px 0;
  }
  .contact-tab svg { width: 16px; height: 16px; fill: var(--paper); }
  .contact-list {
    position: absolute; left: 62px; bottom: 10px;
    list-style: none; color: var(--ink);
    font-size: 14px; line-height: 28px;
    white-space: nowrap;
  }
  .front-band { position: absolute; right: 0; bottom: 0; }
</style>
</head>
<body>

  <section class="card card--back" aria-label="Card back">
    <div class="wordmark">
      <span class="wordmark__name">BRIGHTLINE</span>
      <span class="wordmark__service">TATTOO REMOVAL</span>
    </div>
    <p class="website">www.brightlinetattooremoval.example</p>
  </section>

  <section class="card card--front" aria-label="Card front">
    <div class="wordmark">
      <span class="wordmark__name">BRIGHTLINE</span>
      <span class="wordmark__service">TATTOO REMOVAL</span>
    </div>

    <div class="person-rule"></div>
    <div class="person">
      <p class="person__name">Melissa <strong>Thornbury</strong></p>
      <p class="person__title">Chief Executive Offer</p>
      <p class="person__address">4615 Oakmere Pkwy, Suite 210<br>Raleigh, NC 27654</p>
    </div>

    <svg class="front-band" width="200" height="110" viewBox="0 0 200 110" aria-hidden="true">
      <path d="M0 110 L30 110 C45 110 48 92 50 78 C52 62 60 56 80 56 L200 56 L200 110 Z" fill="var(--ink)"/>
    </svg>

    <div class="contact-tab" aria-hidden="true">
      <svg viewBox="0 0 24 24"><path d="M3 8c0-3 4-5 9-5s9 2 9 5v2h-5V8H8v2H3zM6 12h12l2 9H4z"/></svg>
      <svg viewBox="0 0 24 24"><path d="M6.6 10.8a15 15 0 0 0 6.6 6.6l2.2-2.2a1 1 0 0 1 1-.25 11 11 0 0 0 3.6.6 1 1 0 0 1 1 1V20a1 1 0 0 1-1 1A17 17 0 0 1 3 4a1 1 0 0 1 1-1h3.5a1 1 0 0 1 1 1 11 11 0 0 0 .6 3.6 1 1 0 0 1-.25 1z"/></svg>
      <svg viewBox="0 0 24 24"><path d="M7 3h10v5H7zM4 9h16a2 2 0 0 1 2 2v6h-4v4H6v-4H2v-6a2 2 0 0 1 2-2zm4 7v3h8v-3z"/></svg>
      <svg viewBox="0 0 24 24"><path d="M2 5h20v14H2zm2 2v.5l8 5.5 8-5.5V7zm0 3v7h16v-7l-8 5.5z"/></svg>
    </div>
    <ul class="contact-list">
      <li>919.537.2846</li>
      <li>919.362.4178</li>
      <li>919.685.3907</li>
      <li>mthornbury@brightlinetattooremoval.example</li>
    </ul>
  </section>

</body>
</html>
```